Business Card Design

Need a new business card to represent our legal vertical focus. attached is an example of our old business card and newest logo. we would like the card to also identify "Legal Tech" as a tag line of business.

Our new address is
4817 Marlowe Hatchfield Rd.
Suite 518
Cincinnati, OH 45917

we no longer have a fax number.

Target Market(s)

Tech Consulting for Law Firms

Industry/Entity Type

Legal

Contact Information for Business Card

should use logo and colors. we are a b2b company

Font styles to use
Other font styles liked:
• tahoma

Requirements
Must have
• all print should be in lower case just as shown in photos. tag line should not
Should not have
• pinstripes or drop shadows

```html
<!DOCTYPE html>
<html lang="en">
<head>
<meta charset="utf-8">
<title>lumenbridge legal tech – business card</title>
<link rel="stylesheet" href="https://fonts.googleapis.com/css2?family=Open+Sans:wght@400;600;700&display=swap">
<style>
  :root {
    --backdrop: #d9d9d8;
    --card: #0d0d0d;
    --card-edge: #1a1a1a;
    --accent-orange: #e8552a;
    --accent-blue: #2c3d8f;
    --ink-white: #ffffff;
    --ink-grey: #5c5c5c;
    --ink-soft: #bdbdbd;
    --divider: #2a2a2a;
  }
  * { box-sizing: border-box; margin: 0; padding: 0; }
  html, body {
    width: 1200px;
    height: 900px;
    overflow: hidden;
    background: var(--backdrop);
    font-family: "Open Sans", Tahoma, sans-serif;
  }
  .canvas {
    position: relative;
    width: 1200px;
    height: 900px;
  }
  .card {
    position: absolute;
    left: 300px;
    width: 600px;
    height: 343px;
    background: radial-gradient(ellipse at 50% 40%, var(--card-edge), var(--card) 70%);
    overflow: hidden;
  }
  .card--front { top: 90px; }
  .card--back  { top: 467px; }

  /* wordmark */
  .wordmark {
    position: absolute;
    display: flex;
    flex-direction: column;
    align-items: flex-end;
  }
  .wordmark__row {
    display: flex;
    align-items: center;
    gap: 10px;
  }
  .wordmark__dot {
    width: 14px;
    height: 14px;
    border-radius: 50%;
  }
  .wordmark__name {
    font-weight: 700;
    font-size: 42px;
    line-height: 1;
    letter-spacing: -0.5px;
  }
  .wordmark__tagline {
    margin-top: 6px;
    font-size: 15px;
    letter-spacing: 11px;
    color: var(--ink-grey);
    margin-right: -11px;
  }
  .card--front .wordmark {
    left: 0; right: 0;
    top: 124px;
    align-items: center;
  }
  .card--front .wordmark__name { color: var(--accent-orange); }
  .card--front .wordmark__dot { background: var(--accent-blue); }
  .card--front .wordmark__tagline { align-self: center; margin-left: 120px; }

  .card--back .wordmark {
    right: 34px;
    top: 88px;
  }
  .card--back .wordmark__name { color: var(--ink-white); font-size: 36px; }
  .card--back .wordmark__dot { background: var(--ink-white); width: 12px; height: 12px; }
  .card--back .wordmark__tagline { font-size: 13px; letter-spacing: 9px; margin-right: -9px; }

  /* person */
  .person {
    position: absolute;
    left: 38px;
    top: 104px;
  }
  .person__name {
    color: var(--accent-orange);
    font-size: 24px;
    font-weight: 400;
    line-height: 1.2;
  }
  .person__title {
    color: var(--ink-white);
    font-size: 15px;
    margin-top: 2px;
  }

  .divider {
    position: absolute;
    left: 250px;
    right: 30px;
    top: 188px;
    height: 1px;
    background: var(--divider);
  }

  /* address */
  .address {
    position: absolute;
    left: 38px;
    bottom: 32px;
    font-style: normal;
    color: var(--ink-soft);
    font-size: 14px;
    line-height: 22px;
  }

  /* contact */
  .contact {
    position: absolute;
    right: 28px;
    top: 220px;
    list-style: none;
  }
  .contact__item {
    display: flex;
    justify-content: flex-end;
    align-items: center;
    gap: 10px;
    color: var(--accent-orange);
    font-size: 17px;
    line-height: 24px;
  }
  .contact__icon {
    width: 12px;
    height: 12px;
    flex: none;
  }
</style>
</head>
<body>
<main class="canvas">

  <section class="card card--front" aria-label="card front">
    <div class="wordmark">
      <div class="wordmark__row">
        <span class="wordmark__dot"></span>
        <span class="wordmark__name">lumenbridge</span>
      </div>
      <span class="wordmark__tagline">Legal Tech</span>
    </div>
  </section>

  <section class="card card--back" aria-label="card back">
    <div class="person">
      <p class="person__name">daniel harper</p>
      <p class="person__title">managing director</p>
    </div>

    <div class="wordmark">
      <div class="wordmark__row">
        <span class="wordmark__dot"></span>
        <span class="wordmark__name">lumenbridge</span>
      </div>
      <span class="wordmark__tagline">Legal Tech</span>
    </div>

    <div class="divider"></div>

    <address class="address">
      4817 marlowe hatchfield rd.<br>
      suite 518<br>
      cincinnati, oh 45917
    </address>

    <ul class="contact">
      <li class="contact__item">123.456.7890
        <svg class="contact__icon" viewBox="0 0 12 12" aria-hidden="true"><rect x="3" y="0.5" width="6" height="11" rx="1" fill="none" stroke="#fff" stroke-width="1"/><line x1="5" y1="9.5" x2="7" y2="9.5" stroke="#fff"/></svg>
      </li>
      <li class="contact__item">123.456.7890
        <svg class="contact__icon" viewBox="0 0 12 12" aria-hidden="true"><path d="M1 4 Q6 0 11 4 L9.5 5.5 L8 4.5 L4 4.5 L2.5 5.5 Z" fill="#fff"/><rect x="3" y="6" width="6" height="5" rx="1" fill="#fff"/></svg>
      </li>
      <li class="contact__item">info@youremail.com
        <svg class="contact__icon" viewBox="0 0 12 12" aria-hidden="true"><rect x="0.5" y="2.5" width="11" height="7" fill="#fff"/><path d="M0.5 2.5 L6 7 L11.5 2.5" fill="none" stroke="#0d0d0d" stroke-width="1"/></svg>
      </li>
      <li class="contact__item">www.website.com
        <svg class="contact__icon" viewBox="0 0 12 12" aria-hidden="true"><rect x="0.8" y="4.5" width="6" height="3.4" rx="1.7" transform="rotate(-45 3.8 6.2)" fill="none" stroke="#fff" stroke-width="1.2"/><rect x="5.2" y="4" width="6" height="3.4" rx="1.7" transform="rotate(-45 8.2 5.7)" fill="none" stroke="#fff" stroke-width="1.2"/></svg>
      </li>
    </ul>
  </section>

</main>
</body>
</html>
```